Business Card Update, need to bring life to the card, two sided color

We need a new business card design, are moving and changing addresses and need a new look, we have the logos already attached but need a new style moving forward. Can incorporate the color of the logo (The Green) as well, maybe a solid back? We deal with safety products revolving around static electricity and safety lighting. Would like to keep same font in second logo as well.

Target Market(s)

Electrical Safety, Lighting

Contact Information for Business Card

Dale Fenwick
Vice President
Office: 770-555-4821
Cell: 770-555-3067
dale@tkfenwick.example
www.tkfenwick.example
4700 West Harbor Boulevard
Suite #150
Roswell, GA 30076

Font styles to use
Serif
Sans Serif

Requirements
Must have
• Since 1918
Nice to have
• Could use the 100 Year Logo for back of card, would like the back of card to be the same green as logo.
Should not have
• No black cards please.

```html
<!DOCTYPE html>
<html lang="en">
<head>
<meta charset="utf-8">
<title>T.K. Fenwick Business Card</title>
<link rel="stylesheet" href="https://fonts.googleapis.com/css2?family=Open+Sans:wght@400;600;700&display=swap">
<style>
  :root {
    --page-bg: #e6e8e6;
    --brand-green: #1a9f5c;
    --brand-green-dark: #137a46;
    --front-bg: #f7f8f6;
    --front-bg-edge: #eceeeb;
    --text-white: #ffffff;
    --text-soft-white: #e4f4ea;
    --text-dark: #3b3f3d;
    --rule-grey: #cfd3d0;
    --mark-shade-light: rgba(255, 255, 255, 0.08);
    --mark-shade-dark: rgba(0, 0, 0, 0.035);
  }
  * { margin: 0; padding: 0; box-sizing: border-box; }
  html, body {
    width: 1200px;
    height: 900px;
    overflow: hidden;
    background: var(--page-bg);
    font-family: "Open Sans", Arial, sans-serif;
  }
  .stage { position: relative; width: 1200px; height: 900px; }

  .card {
    position: absolute;
    left: 300px;
    width: 600px;
    height: 343px;
    border-radius: 22px;
    overflow: hidden;
    box-shadow: 0 14px 32px rgba(0, 0, 0, 0.18);
  }
  .card--back {
    top: 88px;
    background: linear-gradient(135deg, var(--brand-green), var(--brand-green-dark));
  }
  .card--front {
    top: 468px;
    background: linear-gradient(135deg, var(--front-bg), var(--front-bg-edge));
  }

  .card__mark-area {
    position: absolute;
    left: -170px;
    top: -40px;
    width: 320px;
    height: 420px;
    border-radius: 50%;
  }
  .card--back .card__mark-area { background: var(--mark-shade-light); }
  .card--front .card__mark-area { background: var(--mark-shade-dark); }

  .lockup {
    position: absolute;
    display: flex;
    align-items: center;
    gap: 14px;
  }
  .lockup__dot {
    width: 64px;
    height: 64px;
    border-radius: 50%;
    flex: none;
  }
  .lockup__name { font-weight: 700; line-height: 1.08; }
  .lockup__title { display: block; font-size: 26px; }
  .lockup__sub { display: block; font-size: 13px; }

  .card--back .lockup { left: 150px; top: 112px; }
  .card--back .lockup__dot { background: var(--text-white); }
  .card--back .lockup__name { color: var(--text-white); }

  .card__since {
    position: absolute;
    left: 228px;
    top: 192px;
    color: var(--text-soft-white);
    font-size: 12px;
    font-weight: 600;
    letter-spacing: 2px;
    text-transform: uppercase;
  }

  .card__website {
    position: absolute;
    right: 110px;
    bottom: 70px;
    color: var(--text-soft-white);
    font-size: 13px;
  }

  .card--front .lockup { left: 236px; top: 60px; }
  .card--front .lockup__dot { background: var(--brand-green); }
  .card--front .lockup__name { color: var(--brand-green); }

  .card__rule {
    position: absolute;
    left: 230px;
    right: 40px;
    top: 158px;
    height: 1px;
    background: var(--rule-grey);
  }

  .person { position: absolute; left: 48px; top: 176px; }
  .person__name {
    color: var(--brand-green);
    font-size: 21px;
    font-weight: 600;
    text-transform: uppercase;
    line-height: 28px;
  }
  .person__role { color: var(--text-dark); font-size: 14px; line-height: 20px; }

  .contacts { list-style: none; margin-top: 12px; }
  .contacts__item {
    display: flex;
    align-items: center;
    gap: 8px;
    color: var(--text-dark);
    font-size: 15px;
    line-height: 22px;
  }
  .contacts__icon { width: 13px; height: 13px; fill: var(--brand-green); flex: none; }

  .address {
    position: absolute;
    right: 40px;
    top: 180px;
    text-align: right;
    color: var(--text-dark);
    font-size: 15px;
    line-height: 21px;
    font-style: normal;
  }
</style>
</head>
<body>
<main class="stage">

  <section class="card card--back" aria-label="Card back">
    <div class="card__mark-area" role="img" aria-label="Faint large brand mark decoration"></div>
    <div class="lockup">
      <span class="lockup__dot"></span>
      <p class="lockup__name">
        <span class="lockup__title">T.K. Fenwick</span>
        <span class="lockup__sub">Manufacturing Company, Inc.</span>
      </p>
    </div>
    <p class="card__since">Since 1918</p>
    <p class="card__website">www.tkfenwick.example</p>
  </section>

  <section class="card card--front" aria-label="Card front">
    <div class="card__mark-area" role="img" aria-label="Faint large brand mark decoration"></div>
    <div class="lockup">
      <span class="lockup__dot"></span>
      <p class="lockup__name">
        <span class="lockup__title">T.K. Fenwick</span>
        <span class="lockup__sub">Manufacturing Company, Inc.</span>
      </p>
    </div>
    <div class="card__rule"></div>

    <div class="person">
      <h1 class="person__name">Dale Fenwick</h1>
      <p class="person__role">Vice President</p>
      <ul class="contacts">
        <li class="contacts__item">
          <svg class="contacts__icon" viewBox="0 0 16 16" aria-hidden="true"><path d="M3 1h3l1.5 4-2 1.3a9 9 0 0 0 4.2 4.2L11 8.5l4 1.5v3a2 2 0 0 1-2 2A12 12 0 0 1 1 3a2 2 0 0 1 2-2z"/></svg>
          770-555-4821
        </li>
        <li class="contacts__item">
          <svg class="contacts__icon" viewBox="0 0 16 16" aria-hidden="true"><path d="M4.5 0h7A1.5 1.5 0 0 1 13 1.5v13a1.5 1.5 0 0 1-1.5 1.5h-7A1.5 1.5 0 0 1 3 14.5v-13A1.5 1.5 0 0 1 4.5 0zM5 2v10h6V2zm3 11a1 1 0 1 0 0 2 1 1 0 0 0 0-2z"/></svg>
          770-555-3067
        </li>
        <li class="contacts__item">
          <svg class="contacts__icon" viewBox="0 0 16 16" aria-hidden="true"><path d="M1 3h14v1.2L8 9 1 4.2zm0 2.6 7 4.8 7-4.8V13H1z"/></svg>
          dale@tkfenwick.example
        </li>
      </ul>
    </div>

    <address class="address">
      4700 West Harbor Boulevard<br>
      Suite #150<br>
      Roswell, GA 30076
    </address>
  </section>

</main>
</body>
</html>
```